BOLD & MINIMALIST DESIGN NEEDED

We want a very bold but minimalistic business card design that is impactful and utilizes both sides of the business card. Our current logo is included for your use.

We want bold fonts and good use of negative space. We don't want the logo to overpower the design.

Target Market(s)

Professionals who are building new commercial buildings.

Industry/Entity Type

Construction

Contact Information for Business Card

Name, Title, email, office phone, cell phone, website

Font styles to use
Serif
Sans Serif

Requirements
Must have
• Bold design!

```html
<!DOCTYPE html>
<html lang="en">
<head>
<meta charset="utf-8">
<title>Ridgeline Build – Business Card</title>
<link href="https://fonts.googleapis.com/css2?family=Montserrat:wght@400;500;700;800&display=swap" rel="stylesheet">
<style>
  :root {
    --backdrop: #dcdcdc;
    --ink: #0c0d0f;
    --paper: #ffffff;
    --accent: #a6d46f;
    --accent-strong: #7cc242;
  }
  html, body {
    margin: 0;
    padding: 0;
    width: 1200px;
    height: 1200px;
    overflow: hidden;
    background: var(--backdrop);
    font-family: "Montserrat", Arial, sans-serif;
  }
  .card {
    position: absolute;
    left: 179px;
    width: 861px;
    height: 495px;
    overflow: hidden;
  }
  .card--front {
    top: 84px;
    background: var(--ink);
    display: flex;
    align-items: center;
    justify-content: center;
  }
  .card--back {
    top: 622px;
    background: var(--paper);
  }
  .card__shapes {
    position: absolute;
    inset: 0;
    width: 100%;
    height: 100%;
  }
  .brand {
    display: flex;
    align-items: center;
    gap: 14px;
  }
  .brand__square {
    width: 30px;
    height: 30px;
    background: var(--accent-strong);
  }
  .brand__name {
    font-weight: 800;
    text-transform: uppercase;
    letter-spacing: 1px;
    line-height: 1;
  }
  .card--front .brand__name {
    color: var(--paper);
    font-size: 42px;
  }
  .card--back .brand {
    position: absolute;
    left: 38px;
    top: 232px;
    gap: 10px;
  }
  .card--back .brand__square {
    width: 22px;
    height: 22px;
  }
  .card--back .brand__name {
    color: var(--ink);
    font-size: 27px;
  }
  .person {
    position: absolute;
    left: 464px;
    top: 116px;
  }
  .person__name {
    margin: 0;
    color: var(--paper);
    font-weight: 700;
    font-size: 32px;
    letter-spacing: 0.6px;
    line-height: 1.15;
  }
  .person__title {
    margin: 0;
    color: var(--accent);
    font-weight: 500;
    font-size: 28px;
    letter-spacing: 1px;
    line-height: 1.15;
  }
  .contacts {
    position: absolute;
    left: 464px;
    top: 232px;
    margin: 0;
    padding: 0;
    list-style: none;
  }
  .contacts__item {
    display: flex;
    align-items: center;
    height: 34px;
    color: var(--paper);
    font-size: 25px;
    letter-spacing: 1px;
  }
  .contacts__icon {
    width: 28px;
    height: 28px;
    margin-right: 12px;
    flex: none;
  }
  .contacts__highlight {
    color: var(--accent);
  }
</style>
</head>
<body>

<section class="card card--front" aria-label="Business card front">
  <div class="brand">
    <span class="brand__square"></span>
    <span class="brand__name">Ridgeline Build</span>
  </div>
</section>

<section class="card card--back" aria-label="Business card back">
  <svg class="card__shapes" viewBox="0 0 1387 796" preserveAspectRatio="none" aria-hidden="true">
    <path d="M522 0 H1387 V796 H555 Q845.5 402 522 0 Z" fill="var(--ink)"/>
    <path d="M542 55 Q799.5 414.5 527 796 H442 Q768 414.5 542 55 Z" fill="var(--accent)"/>
  </svg>

  <div class="brand">
    <span class="brand__square"></span>
    <span class="brand__name">Ridgeline Build</span>
  </div>

  <div class="person">
    <p class="person__name">Name Surename</p>
    <p class="person__title">Director</p>
  </div>

  <ul class="contacts">
    <li class="contacts__item">
      <svg class="contacts__icon" viewBox="0 0 24 24" aria-hidden="true">
        <path d="M6.6 10.8a15 15 0 0 0 6.6 6.6l2.2-2.2a1 1 0 0 1 1-.25 11.4 11.4 0 0 0 3.6.57 1 1 0 0 1 1 1V20a1 1 0 0 1-1 1A17 17 0 0 1 3 4a1 1 0 0 1 1-1h3.5a1 1 0 0 1 1 1c0 1.25.2 2.45.57 3.6a1 1 0 0 1-.25 1z" fill="var(--accent)"/>
        <path d="M14 3a7 7 0 0 1 7 7M14 6.5a3.5 3.5 0 0 1 3.5 3.5" stroke="var(--accent)" stroke-width="1.8" fill="none" stroke-linecap="round"/>
      </svg>
      555-014-2200
    </li>
    <li class="contacts__item">
      <svg class="contacts__icon" viewBox="0 0 24 24" aria-hidden="true">
        <path d="M2 8c0-2 4-4 10-4s10 2 10 4v2h-5V8.5c-1.5-.6-3.2-.9-5-.9s-3.5.3-5 .9V10H2z" fill="var(--accent)"/>
        <path d="M7 11h10l3 5v5H4v-5z" fill="var(--accent)"/>
        <circle cx="12" cy="16" r="2.3" fill="var(--ink)"/>
      </svg>
      555-014-2200
    </li>
    <li class="contacts__item">
      <svg class="contacts__icon" viewBox="0 0 24 24" aria-hidden="true">
        <rect x="2" y="5" width="20" height="14" fill="none" stroke="var(--accent)" stroke-width="1.8"/>
        <path d="M2 5l10 8 10-8M2 19l7.5-7M22 19l-7.5-7" fill="none" stroke="var(--accent)" stroke-width="1.6"/>
      </svg>
      info@ridgeline-build.com
    </li>
    <li class="contacts__item">
      <svg class="contacts__icon" viewBox="0 0 24 24" aria-hidden="true">
        <g fill="none" stroke="var(--accent)" stroke-width="1.6">
          <circle cx="12" cy="12" r="10"/>
          <ellipse cx="12" cy="12" rx="4.5" ry="10"/>
          <path d="M2 12h20M3.5 7h17M3.5 17h17M12 2v20"/>
        </g>
      </svg>
      www.<span class="contacts__highlight">ridgeline-build</span>.com
    </li>
  </ul>
</section>

</body>
</html>
```